sticker for cleaning products

it is in the bottle. products are bio-cleaner. Toilet Cleaner - yellow Sanitary Cleaner - orange Glass Cleaner - light blue All purpose cleaner - green Hand Soap - cream Detergent - olive Detergent - rose bottles is used RUNDA: https://glasbehalterwerk.de/katalog/#Runda shape of the sticker is not geometric. It's something like a cloud / leaf / drop / ?? the sticker has an inner space with only the product name and color. the sticker has an outer space. here we want to mark out "powered by KORVINEL" (our company name, find logo attached)

```html
<!DOCTYPE html>
<html lang="en">
<head>
<meta charset="utf-8">
<title>KORVINEL Refill – Product Stickers</title>
<link href="https://fonts.googleapis.com/css2?family=Josefin+Sans:wght@400;600;700&display=swap" rel="stylesheet">
<style>
  :root {
    --ink: #272625;
    --bronze: #b08a62;
    --paper: #ffffff;
    --toilet: #ffcb05;
    --sanitary: #ee7f1e;
    --glass: #66c2d1;
    --allpurpose: #4bb848;
    --handsoap: #fbe0bd;
    --detergent-olive: #a7c52a;
    --detergent-rose: #ee8480;
  }
  * { margin: 0; padding: 0; box-sizing: border-box; }
  html, body { width: 1200px; height: 1200px; overflow: hidden; background: var(--paper); }
  .sheet {
    width: 1200px; height: 1200px;
    display: flex; flex-direction: column; justify-content: center; gap: 60px;
    font-family: "Josefin Sans", sans-serif;
  }
  .sticker-row { display: flex; justify-content: center; gap: 46px; }
  .sticker { width: 240px; height: 404px; display: block; }
  .sticker__body { fill: var(--ink); }
  .sticker__mark { fill: none; stroke: var(--bronze); stroke-width: 2.2; }
  .sticker__brand { fill: #ffffff; font-size: 12px; font-weight: 600; letter-spacing: 4.2px; }
  .sticker__line { fill: var(--bronze); font-size: 6.5px; letter-spacing: 2.6px; }
  .sticker__name { fill: var(--ink); font-size: 26px; font-weight: 600; }
  .sticker__name--long { font-size: 23px; }
  .sticker__volume { fill: var(--ink); font-size: 11px; font-weight: 700; }
  .fill-toilet { fill: var(--toilet); }
  .fill-sanitary { fill: var(--sanitary); }
  .fill-glass { fill: var(--glass); }
  .fill-allpurpose { fill: var(--allpurpose); }
  .fill-handsoap { fill: url(#handsoap-glow); }
  .fill-olive { fill: var(--detergent-olive); }
  .fill-rose { fill: var(--detergent-rose); }
</style>
</head>
<body>
<svg width="0" height="0" style="position:absolute" aria-hidden="true">
  <defs>
    <radialGradient id="handsoap-glow" cx="0.4" cy="0.4" r="0.7">
      <stop offset="0" stop-color="#fdf0df"/>
      <stop offset="1" stop-color="#f8d6a8"/>
    </radialGradient>
    <symbol id="drop-frame" viewBox="0 0 220 370">
      <path class="sticker__body" d="M138 0 C62 45 8 140 5 262 A105 105 0 0 0 215 262 C215 208 182 172 162 132 C142 92 128 48 138 0 Z"/>
      <circle class="sticker__mark" cx="110" cy="116" r="12"/>
      <text class="sticker__brand" x="112" y="148" text-anchor="middle">KORVINEL</text>
      <text class="sticker__line" x="111" y="159" text-anchor="middle">REFILL</text>
    </symbol>
  </defs>
</svg>

<main class="sheet">
  <div class="sticker-row">
    <svg class="sticker" viewBox="0 0 220 370">
      <use href="#drop-frame"/>
      <circle class="fill-toilet" cx="110" cy="262" r="90"/>
      <text class="sticker__name" x="110" y="256" text-anchor="middle">TOILET</text>
      <text class="sticker__name" x="110" y="284" text-anchor="middle">CLEANER</text>
      <text class="sticker__volume" x="110" y="330" text-anchor="middle">1000 ML</text>
    </svg>
    <svg class="sticker" viewBox="0 0 220 370">
      <use href="#drop-frame"/>
      <circle class="fill-sanitary" cx="110" cy="262" r="90"/>
      <text class="sticker__name" x="110" y="256" text-anchor="middle">SANITARY</text>
      <text class="sticker__name" x="110" y="284" text-anchor="middle">CLEANER</text>
      <text class="sticker__volume" x="110" y="330" text-anchor="middle">1000 ML</text>
    </svg>
    <svg class="sticker" viewBox="0 0 220 370">
      <use href="#drop-frame"/>
      <circle class="fill-glass" cx="110" cy="262" r="90"/>
      <text class="sticker__name" x="110" y="256" text-anchor="middle">GLASS</text>
      <text class="sticker__name" x="110" y="284" text-anchor="middle">CLEANER</text>
      <text class="sticker__volume" x="110" y="330" text-anchor="middle">1000 ML</text>
    </svg>
  </div>
  <div class="sticker-row">
    <svg class="sticker" viewBox="0 0 220 370">
      <use href="#drop-frame"/>
      <circle class="fill-allpurpose" cx="110" cy="262" r="90"/>
      <text class="sticker__name sticker__name--long" x="110" y="256" text-anchor="middle">ALL PURPOSE</text>
      <text class="sticker__name sticker__name--long" x="110" y="282" text-anchor="middle">CLEANER</text>
      <text class="sticker__volume" x="110" y="330" text-anchor="middle">1000 ML</text>
    </svg>
    <svg class="sticker" viewBox="0 0 220 370">
      <use href="#drop-frame"/>
      <circle class="fill-handsoap" cx="110" cy="262" r="90"/>
      <text class="sticker__name" x="110" y="272" text-anchor="middle">HAND SOAP</text>
      <text class="sticker__volume" x="110" y="330" text-anchor="middle">1000 ML</text>
    </svg>
    <svg class="sticker" viewBox="0 0 220 370">
      <use href="#drop-frame"/>
      <circle class="fill-olive" cx="110" cy="262" r="90"/>
      <text class="sticker__name" x="110" y="272" text-anchor="middle">DETERGENT</text>
      <text class="sticker__volume" x="110" y="330" text-anchor="middle">1000 ML</text>
    </svg>
    <svg class="sticker" viewBox="0 0 220 370">
      <use href="#drop-frame"/>
      <circle class="fill-rose" cx="110" cy="262" r="90"/>
      <text class="sticker__name" x="110" y="272" text-anchor="middle">DETERGENT</text>
      <text class="sticker__volume" x="110" y="330" text-anchor="middle">1000 ML</text>
    </svg>
  </div>
</main>
</body>
</html>
```